Health supplement brand needs a new logo for flagship product launch

I have attached a Word document to the brief which gives more detail.

There are 3 different products that we will sell. The label should be interchangeable across all 3 products, where only the colours change. This requires both a selection of a font typface to match our style and a new image embedded in the logo.

Target Market(s)

The target customer is women aged between 25 and 60. We would like to cross over between both audiences, without ruling one out

Font styles to use
Sans Serif

Requirements
Must have
• - It must be eye catching, i.e. people need to stop scrolling when they see it.
- It must have contemporary colours that are popular with women, i.e. pinks, apricots, dark greens, mustards, etc
- The image needs to be very feminine, just like the target audience
- The label must evoke some emotion, yet still be a little bit fun without being too serious.
- The label must use this image below as the main foundation. I have included the EPS file with this email.
Nice to have
• - We want to be somewhere in the middle, as in, the right price point accessible for most people, but still with a bit of class, fun and femininity
Should not have
• - We also don’t want it to look like “just another” nutritional brand selling Crestwyn Blends

```html
<!DOCTYPE html>
<html lang="en">
<head>
<meta charset="utf-8">
<title>SOLAFORM Collagen Label</title>
<link rel="stylesheet" href="https://fonts.googleapis.com/css2?family=Ubuntu:wght@300;400;500&display=swap">
<style>
  :root {
    --paper: #ffffff;
    --frame: #2a2a2a;
    --brand-pink: #fda4b8;
    --band-blush: #f6c1b8;
    --band-rose: #fb6488;
    --band-edge: #7a7f9a;
    --art-cream: #fdf0e4;
    --art-peach: #f4c79a;
    --ink: #161616;
  }
  * { margin: 0; padding: 0; box-sizing: border-box; }
  html, body {
    width: 1200px; height: 1200px; overflow: hidden;
    background: var(--paper);
  }
  .canvas { position: relative; width: 1200px; height: 1200px; overflow: hidden; }
  .label-frame {
    position: absolute; left: 145px; top: 100px;
    width: 879px; height: 1120px;
    border: 1.5px solid var(--frame);
  }
  .brand-name {
    position: absolute; left: 172px; top: 118px;
    font-family: "Ubuntu", sans-serif; font-weight: 500;
    font-size: 80px; line-height: 1;
    letter-spacing: 6px;
    color: var(--brand-pink);
    white-space: nowrap;
  }
  .product-name {
    position: absolute; right: 200px; top: 478px;
    font-family: "Ubuntu", sans-serif; font-weight: 500;
    font-size: 84px; line-height: 1;
    letter-spacing: 1px;
    color: var(--brand-pink);
    white-space: nowrap;
  }
  .tagline {
    position: absolute; right: 190px; top: 572px;
    font-family: "Ubuntu", sans-serif; font-weight: 300;
    font-size: 56px; line-height: 1;
    letter-spacing: 8px;
    color: var(--brand-pink);
    white-space: nowrap;
  }
  .tagline .dash { font-size: 40px; vertical-align: middle; margin: 0 16px; }
  .descriptor {
    position: absolute; right: 196px;
    font-family: "Ubuntu", sans-serif; font-weight: 400;
    font-size: 26px; line-height: 1;
    letter-spacing: 2.2px;
    color: var(--ink);
    white-space: nowrap;
    word-spacing: 4px;
  }
  .descriptor--type { top: 656px; }
  .descriptor--benefits { top: 699px; right: 190px; word-spacing: 14px; }
  .band {
    position: absolute; left: 145px; width: 879px;
    border-top: 1.5px solid var(--band-edge);
  }
  .band--blush { top: 772px; height: 112px; background: var(--band-blush); }
  .band--rose {
    top: 884px; height: 226px; background: var(--band-rose);
    border-bottom: 1.5px solid var(--band-edge);
  }
  .hero-art {
    position: absolute; left: 381px; top: 772px;
    width: 412px; height: 342px;
    background: linear-gradient(100deg, var(--art-cream) 0%, var(--art-cream) 55%, var(--art-peach) 80%, var(--art-cream) 100%);
  }
</style>
</head>
<body>
<main class="canvas">
  <div class="label-frame"></div>

  <div class="brand-name">SOLAFORM</div>

  <div class="product-name">collagen</div>
  <div class="tagline"><span class="dash">-</span>Soft Glow<span class="dash">-</span></div>

  <p class="descriptor descriptor--type">Unflavoured 100% bovine Collagen Powder</p>
  <p class="descriptor descriptor--benefits">Hair Skin Nails Joints Muscles</p>

  <div class="band band--blush"></div>
  <div class="band band--rose"></div>

  <div class="hero-art" role="img" aria-label="Line-art illustration of a seated woman seen from behind beside blooming peach and mustard flowers with dark green leaves"></div>
</main>
</body>
</html>
```